Maple Sprout Menu (Vegetarian Restaurant Concept)

Maple Sprout is a new concept fast casual restaurant
renders are attached so you can see the style of restaurant
Maple Sproute is a vibrant and modern Vegetarian fast casual restaurant concept that mixes fresh food, energy, great décor, and a comfortable, welcoming atmosphere to provide a memorable and all Vegetarian dining experience.
Our Mission is to be top of mind when consumers think Vegetarian food!
Updates
Need extra days to review
Target Market(s)
the menu is vegetarian and appeals to a broad demographic in USA
Font styles to use
Colors
Designer to choose colors to be used in the design.
Requirements
Must have
- well colored and well laid out menu - should not be cartoonish
Nice to have
- For Phots please use the shots in this file:
- https://www.filecrate-share.net/sh/qtrv8knw2lpa5zc/BBBxR_pLmNoQwEE4J_TKX_Va?dl=0
- note these are untouched and you are free to change as needed
Should not have
- Should not be cartoonish - nor kives, forks etc in the design

```html
<!DOCTYPE html>
<html lang="en">
<head>
<meta charset="utf-8">
<title>Maple Sprout Menu</title>
<link rel="stylesheet" href="https://fonts.googleapis.com/css2?family=Abril+Fatface&family=Oswald:wght@500;600&display=swap">
<style>
  :root {
    --panel-rust: #bd7341;
    --board-dark: #1f2327;
    --ink-light: #ffffff;
    --note-rust: #c0703f;
    --burger-tone: radial-gradient(circle at 50% 50%, #8a4e32 0%, #b98c62 55%, #d7c3a3 100%);
    --noodle-tone: radial-gradient(circle at 50% 50%, #8fb04a 0%, #6f8f3c 60%, #5b6b45 100%);
    --berry-tone: radial-gradient(circle at 50% 50%, #5a1f2a 0%, #8a2632 55%, #d94a4a 85%, #f3f3f3 100%);
  }
  * { margin: 0; padding: 0; box-sizing: border-box; }
  html, body { width: 849px; height: 1200px; overflow: hidden; background: var(--board-dark); }
  .menu { position: relative; width: 849px; height: 1200px; background: var(--board-dark); overflow: hidden; }
  .side-panel { position: absolute; left: 0; top: 0; width: 302px; height: 1200px; background: var(--panel-rust); }
  .side-rule { position: absolute; left: 1px; top: 818px; width: 1px; height: 276px; background: rgba(255,255,255,0.6); }
  .dish-photo { position: absolute; left: 16px; width: 262px; height: 262px; border-radius: 50%; }
  .dish-photo.burger { top: 115px; background: var(--burger-tone); }
  .dish-photo.noodles { top: 470px; background: var(--noodle-tone); }
  .dish-photo.berries { top: 823px; background: var(--berry-tone); }

  .section-title {
    position: absolute; left: 344px;
    font-family: "Abril Fatface", serif; font-weight: 400;
    font-size: 46px; line-height: 54px; color: var(--ink-light);
    letter-spacing: 0.5px;
  }
  .section-rule { position: absolute; left: 342px; width: 465px; height: 1px; background: var(--ink-light); }
  .item {
    position: absolute; left: 344px;
    font-family: "Oswald", sans-serif; font-weight: 600;
    font-size: 24px; line-height: 33px; color: var(--ink-light);
  }
  .item-note {
    position: absolute; left: 344px;
    font-family: "Oswald", sans-serif; font-weight: 500;
    font-size: 15px; line-height: 21.5px; color: var(--note-rust);
  }
</style>
</head>
<body>
<main class="menu">
  <aside class="side-panel">
    <div class="dish-photo burger" role="img" aria-label="Photo of a stacked sweet potato black bean veggie burger"></div>
    <div class="dish-photo noodles" role="img" aria-label="Photo of soba noodles with sugar snap peas, edamame and red pepper"></div>
    <div class="dish-photo berries" role="img" aria-label="Photo of a strawberry dessert bowl topped with coconut"></div>
    <div class="side-rule"></div>
  </aside>

  <h2 class="section-title" style="top:38px;">BURGERS, WRAPS<br>&amp; SANDWICHES</h2>
  <div class="section-rule" style="top:144px;"></div>

  <p class="item" style="top:186px;">Sweet Potato, Black Bean Veggie<br>Burgers with Cabbage Pepita Slaw</p>
  <p class="item" style="top:268px;">Roasted Vejjie, Arugula<br>and Hummus Wraps</p>
  <p class="item" style="top:350px;">Garden Burger</p>
  <p class="item" style="top:399px;">Beans and Greens Quesadillas</p>
  <p class="item-note" style="top:438px;">greens, Mexican cheese, beans and avocado, with salsa</p>
  <p class="item" style="top:478px;">Vejjie Burrito</p>
  <p class="item-note" style="top:517px;">greens, Mexican cheese, beans, brown rice,<br>roasted chili corn and avocado, with ancho<br>chili salsa, wheat tortilla</p>

  <h2 class="section-title" style="top:628px;">BOWLS</h2>
  <div class="section-rule" style="top:681px;"></div>
  <p class="item" style="top:719px;">Roasted Vegetable, and Spinach Bowl</p>
  <p class="item" style="top:768px;">Sugar Snap Pea and Carrot Soba Noodles</p>
  <p class="item" style="top:817px;">Whole Grain and Vegetable Buddha Bowl</p>
  <p class="item" style="top:866px;">Orange and Pistacio Quinoa</p>

  <h2 class="section-title" style="top:948px;">DESSERT</h2>
  <div class="section-rule" style="top:999px;"></div>
  <p class="item" style="top:1042px;">Strawberry Balsamic Ice Cream Sundae</p>
  <p class="item" style="top:1090px;">Exotic Fruit Bowl</p>
  <p class="item" style="top:1138px;">White and Dark Oatmeal Cookie</p>
</main>
</body>
</html>
```